Website Design for Landscaping/Concrete Company

I need a website that is informative about what my company does and also offers before and after pictures of completed work. I already have a logo. The website must say "FREE ESTIMATES" somewhere and list a phone number. I would like to stick with the logo colors or similar (black and lime green).
Services Offered by Tomlet Builders:
Landscaping
Mowing
Concrete
Sidewalks
Brush Removal
Land Beautification

Please list the company name in large letters TOMLET BUILDERS
and also the contact information in large font.

Right now I am looking for a somewhat coverpage for my website. I don't have a lot of information for people to point and click on yet. Id like to get a coverpage to get my name out and then have a designer come back in a few months and update with more pictures and information.
Updates

If allowed please submit projects after due date. I made a mistake and only posted for one day. Thanks.

Coding

Coded - Design and coding required

```html
<!DOCTYPE html>
<html lang="en">
<head>
<meta charset="utf-8">
<title>Tomlet Builders – Landscaping &amp; Concrete</title>
<link href="https://fonts.googleapis.com/css2?family=Michroma&family=Roboto:ital,wght@0,400;0,500;0,700;1,400&display=swap" rel="stylesheet">
<style>
:root{
  --lime:#9dbd1d;
  --lime-dark:#86a314;
  --ink:#1d1d1d;
  --text:#444;
  --muted:#8a8a8a;
  --panel:#f3f2f1;
  --white:#fff;
  --black:#0d0d0d;
  --line:#e2e2e2;
}
*{box-sizing:border-box;margin:0;padding:0}
html,body{width:1200px;height:5089px;overflow:hidden}
body{font-family:'Roboto',Arial,sans-serif;color:var(--ink);background:var(--white);position:relative}
.display{font-family:'Michroma','Roboto',sans-serif;font-weight:400}
.btn{display:inline-flex;align-items:center;justify-content:center;background:var(--lime);color:var(--white);font:700 14px 'Roboto',sans-serif;text-transform:uppercase;letter-spacing:.2px;border-radius:2px}
.abs{position:absolute}
.section-title{position:absolute;left:0;width:1200px;text-align:center;font-size:31px;letter-spacing:1px;color:var(--ink)}
.section-title::after{content:"";display:block;width:48px;height:4px;background:var(--lime);margin:14px auto 0}

/* header */
.site-header{position:absolute;top:0;left:0;width:1200px;height:103px;background:var(--white)}
.brand{position:absolute;left:100px;top:22px;display:flex;align-items:center;gap:10px}
.brand-mark{width:26px;height:26px;background:var(--ink)}
.brand-name{font-family:'Michroma',sans-serif;font-size:12px;line-height:15px;color:var(--ink);width:110px}
.nav{position:absolute;top:70px;left:0;width:1200px;height:20px}
.nav a{position:absolute;font:500 15px 'Roboto',sans-serif;color:var(--ink);text-decoration:none}
.estimate{position:absolute;left:895px;top:9px;display:flex;align-items:center;gap:10px}
.estimate-icon{width:44px;height:44px;border-radius:50%;background:var(--lime);display:flex;align-items:center;justify-content:center}
.estimate small{display:block;font:700 12px 'Roboto',sans-serif}
.estimate strong{display:block;font:700 19px 'Roboto',sans-serif;white-space:nowrap}

/* hero */
.hero{position:absolute;top:103px;left:0;width:1200px;height:589px;background:linear-gradient(180deg,#c9c3b5 0%,#7d8a55 30%,#5e8f2c 60%,#6ea434 100%)}
.hero-title{position:absolute;left:100px;top:165px;font-size:43px;line-height:48px;color:var(--white)}
.hero-text{position:absolute;left:102px;top:272px;width:430px;font-size:14px;line-height:22px;color:var(--white)}
.hero .btn{position:absolute;left:102px;top:339px;width:146px;height:42px}
.hero-arrow{position:absolute;top:290px}
.dots{position:absolute;top:533px;left:565px;display:flex;gap:7px}
.dots span{width:11px;height:11px;border-radius:50%;border:1.5px solid var(--white)}
.dots span.on{background:var(--white)}

/* services */
.services-grid{position:absolute;top:870px;left:99px;display:grid;grid-template-columns:repeat(3,320px);column-gap:20px;row-gap:20px}
.service-card{height:412px;background:var(--white);box-shadow:0 2px 12px rgba(0,0,0,.12);position:relative}
.service-photo{height:233px}
.service-icon{position:absolute;right:32px;top:205px;width:56px;height:56px;border-radius:50%;background:var(--white);box-shadow:0 1px 6px rgba(0,0,0,.15);display:flex;align-items:center;justify-content:center}
.service-card h3{position:absolute;left:14px;top:258px;font:700 17px 'Roboto',sans-serif;text-transform:uppercase}
.service-card p{position:absolute;left:14px;top:285px;width:292px;font-size:12.5px;line-height:20px;color:var(--muted)}
.service-card .btn{position:absolute;left:14px;top:361px;width:128px;height:38px;font-size:13px}

/* welcome */
.welcome{position:absolute;top:1823px;left:0;width:1200px;height:513px;background:var(--panel)}
.welcome-photo{position:absolute;left:0;top:0;width:600px;height:513px;background:linear-gradient(160deg,#2f5a22 0%,#7fa048 45%,#b8a27a 70%,#5c8b2e 100%)}
.welcome-kicker{position:absolute;left:651px;top:78px;font:500 20px/24px 'Roboto',sans-serif}
.welcome-title{position:absolute;left:651px;top:108px;font-size:27px;line-height:36px;letter-spacing:.5px;white-space:nowrap}
.welcome-text{position:absolute;left:651px;top:172px;width:450px;font-size:12.5px;line-height:22px;color:var(--text)}
.welcome .btn{position:absolute;left:651px;top:390px;width:145px;height:42px}

/* why choose us */
.feature{position:absolute;width:365px}
.feature-icon{position:absolute;top:0;width:83px;height:83px;border-radius:50%;background:var(--lime);display:flex;align-items:center;justify-content:center}
.feature h3{position:absolute;top:2px;font:700 17px 'Roboto',sans-serif;text-transform:uppercase;white-space:nowrap}
.feature p{position:absolute;top:28px;width:262px;font-size:13.5px;line-height:21px;color:var(--text)}
.feature.left .feature-icon{left:0}
.feature.left h3,.feature.left p{left:107px}
.feature.right .feature-icon{right:0}
.feature.right h3,.feature.right p{left:0}
.divider{position:absolute;height:1px;background:var(--line);width:365px;top:2657px}
.center-brand{position:absolute;left:510px;top:2590px;width:180px;text-align:center}
.center-brand .brand-mark{width:40px;height:40px;margin:0 auto 14px}
.center-brand span{font-family:'Michroma',sans-serif;font-size:17px;line-height:26px;color:var(--ink)}

/* testimonials */
.testimonials{position:absolute;top:2906px;left:0;width:1200px;height:434px;background:linear-gradient(180deg,#ece8dc 0%,#e4e2cf 50%,#d9dcb8 100%)}
.testimonials .section-title{top:60px}
.quote-mark{position:absolute;top:135px;left:545px;width:110px;display:flex;align-items:center;justify-content:center;gap:8px;font:700 26px/26px 'Roboto',sans-serif;color:var(--ink)}
.quote-mark i{display:block;width:30px;height:1px;background:var(--ink)}
.quote-text{position:absolute;top:170px;left:240px;width:720px;text-align:center;font-style:italic;font-size:15px;line-height:25px;color:var(--text)}
.reviewer{position:absolute;top:316px;left:525px;display:flex;align-items:center;gap:12px}
.avatar{width:42px;height:42px;border-radius:50%;background:#b49a82}
.reviewer strong{display:block;font:700 14px 'Roboto',sans-serif}
.reviewer small{display:block;font-size:11px;color:var(--muted)}
.t-arrow{position:absolute;top:187px}

/* projects */
.project{position:absolute;width:486px;height:307px;display:flex}
.project .half{flex:1;height:100%}
.project .half+.half{border-left:2px solid var(--white)}
.project-toggle{position:absolute;left:222px;top:132px;width:42px;height:42px;border-radius:50%;background:var(--white);display:flex;align-items:center;justify-content:center}

/* call to action */
.cta{position:absolute;top:4300px;left:0;width:1200px;height:433px;background:linear-gradient(180deg,#3a2a1e 0%,#2b2b1f 50%,#233019 100%)}
.cta h2{position:absolute;top:78px;left:0;width:1200px;text-align:center;color:var(--white);font-size:30px;line-height:40px;letter-spacing:1px}
.phone-box{position:absolute;left:455px;top:178px;width:290px;height:62px;border:2px solid var(--white);display:flex;align-items:center;color:var(--white)}
.phone-icon{flex:none;width:58px;height:100%;display:flex;align-items:center;justify-content:center;border-right:2px solid var(--white)}
.phone-number{flex:1;text-align:center;font:400 29px/1 'Roboto',sans-serif;white-space:nowrap}
.cta .btn{position:absolute;left:522px;top:297px;width:156px;height:42px}

/* footer */
.site-footer{position:absolute;top:4733px;left:0;width:1200px;height:356px;background:var(--black);color:var(--white)}
.footer-brand{position:absolute;left:100px;top:82px;width:160px;text-align:center}
.footer-brand .brand-mark{width:56px;height:56px;background:var(--white);margin:0 auto 16px}
.footer-brand span{font-family:'Michroma',sans-serif;font-size:18px;line-height:26px}
.footer-col{position:absolute;top:76px}
.footer-col h4{font:500 16px 'Roboto',sans-serif;margin-bottom:14px;text-transform:uppercase}
.footer-col li{list-style:none;font-size:13px;line-height:24px}
.contact-row{display:flex;align-items:center;gap:14px;margin-bottom:10px;font-size:13px;line-height:22px}
.contact-icon{width:36px;height:36px;border-radius:50%;background:var(--white);display:flex;align-items:center;justify-content:center;flex:none}
.social li{display:flex;align-items:center;gap:8px}
.social li::before{content:"";width:8px;height:8px;background:var(--white)}
.footer-rule{position:absolute;left:100px;top:296px;width:1000px;height:1px;background:#333}
.copyright{position:absolute;top:318px;left:0;width:1200px;text-align:center;font-size:12px;color:#ddd}
</style>
</head>
<body>

<header class="site-header">
  <div class="brand"><span class="brand-mark"></span><span class="brand-name">TOMLET BUILDERS</span></div>
  <nav class="nav">
    <a style="left:398px">HOME</a>
    <a style="left:493px">ABOUT US</a>
    <a style="left:624px">SERVICES</a>
    <a style="left:752px">PROJECTS</a>
    <a style="left:886px">REVIEW</a>
    <a style="left:1002px">CONTACT US</a>
  </nav>
  <div class="estimate">
    <span class="estimate-icon"><svg width="22" height="22" viewBox="0 0 24 24"><path d="M6.6 10.8a15 15 0 0 0 6.6 6.6l2.2-2.2c.3-.3.7-.4 1-.2 1.1.4 2.3.6 3.6.6.6 0 1 .4 1 1V20c0 .6-.4 1-1 1A17 17 0 0 1 3 4c0-.6.4-1 1-1h3.5c.6 0 1 .4 1 1 0 1.3.2 2.5.6 3.6.1.3 0 .7-.2 1z" fill="#fff"/></svg></span>
    <div><small>FREE ESTIMATES</small><strong>(555) - 014 - 7720</strong></div>
  </div>
</header>

<section class="hero" role="img" aria-label="Front garden with colourful flower beds and a green lawn before a white house">
  <h1 class="hero-title display">TOMLET<br>BUILDERS</h1>
  <p class="hero-text">Lorem ipsum dolor sit amet, consectetur adipiscing elit, sed do eiusmod tempor incididunt ut labore et dolore magna aliqua.</p>
  <a class="btn">Get a Quote</a>
  <svg class="hero-arrow" style="left:66px" width="18" height="30" viewBox="0 0 18 30"><path d="M15 2 3 15l12 13" stroke="#fff" stroke-width="2" fill="none"/></svg>
  <svg class="hero-arrow" style="left:1116px" width="18" height="30" viewBox="0 0 18 30"><path d="M3 2l12 13L3 28" stroke="#fff" stroke-width="2" fill="none"/></svg>
  <div class="dots"><span class="on"></span><span></span><span></span><span></span></div>
</section>

<section class="services">
  <h2 class="section-title display" style="top:795px">OUR SERVICES</h2>
  <div class="services-grid">
    <article class="service-card">
      <div class="service-photo" role="img" aria-label="Landscaped lawn with shrubs and trees" style="background:linear-gradient(180deg,#cfe3f0,#6f9c3c 55%,#4d7d25)"></div>
      <span class="service-icon"><svg width="30" height="30" viewBox="0 0 30 30" fill="none" stroke="#9dbd1d" stroke-width="2"><circle cx="10" cy="9" r="5"/><path d="M10 14v12M4 26h22M18 12h8v8h-8z"/></svg></span>
      <h3>Landscaping</h3>
      <p>Lorem ipsum dolor sit amet, consur adipiscing elit, sed do eiusmod tempor iniduntut labore et dolore magna aliqua</p>
      <a class="btn">Learn More</a>
    </article>
    <article class="service-card">
      <div class="service-photo" role="img" aria-label="Lawn mower cutting grass" style="background:linear-gradient(180deg,#9cc74a,#4f8a1f)"></div>
      <span class="service-icon"><svg width="30" height="30" viewBox="0 0 30 30" fill="none" stroke="#9dbd1d" stroke-width="2"><path d="M4 4l8 12h12v6H8z"/><circle cx="10" cy="24" r="3"/><circle cx="22" cy="24" r="3"/></svg></span>
      <h3>Mowing</h3>
      <p>Lorem ipsum dolor sit amet, consur adipiscing elit, sed do eiusmod tempor iniduntut labore et dolore magna aliqua</p>
      <a class="btn">Learn More</a>
    </article>
    <article class="service-card">
      <div class="service-photo" role="img" aria-label="Concrete driveway before a garage door" style="background:linear-gradient(180deg,#e8e6e1,#c9c6bf 60%,#a9a59c)"></div>
      <span class="service-icon"><svg width="30" height="30" viewBox="0 0 30 30" fill="none" stroke="#9dbd1d" stroke-width="2"><path d="M3 14l12-6 12 6-12 6zM3 14v5l12 6 12-6v-5"/></svg></span>
      <h3>Concrete</h3>
      <p>Lorem ipsum dolor sit amet, consur adipiscing elit, sed do eiusmod tempor iniduntut labore et dolore magna aliqua</p>
      <a class="btn">Learn More</a>
    </article>
    <article class="service-card">
      <div class="service-photo" role="img" aria-label="Paved garden sidewalk at sunset" style="background:linear-gradient(180deg,#f1d58a,#6f8f3a 45%,#a7a9ad)"></div>
      <span class="service-icon"><svg width="30" height="30" viewBox="0 0 30 30" fill="none" stroke="#9dbd1d" stroke-width="2"><rect x="4" y="7" width="22" height="16"/><path d="M4 13h22M4 18h22M11 7v6M19 13v5M11 18v5"/></svg></span>
      <h3>Sidewalks</h3>
      <p>Lorem ipsum dolor sit amet, consur adipiscing elit, sed do eiusmod tempor iniduntut labore et dolore magna aliqua</p>
      <a class="btn">Learn More</a>
    </article>
    <article class="service-card">
      <div class="service-photo" role="img" aria-label="Raking brush and leaves on a lawn" style="background:linear-gradient(180deg,#8a9a5a,#6d7f3a 50%,#9a8a5a)"></div>
      <span class="service-icon"><svg width="30" height="30" viewBox="0 0 30 30" fill="none" stroke="#9dbd1d" stroke-width="2"><path d="M6 8h18M12 8V5h6v3M8 8l2 18h10l2-18"/></svg></span>
      <h3>Brush Removal</h3>
      <p>Lorem ipsum dolor sit amet, consur adipiscing elit, sed do eiusmod tempor iniduntut labore et dolore magna aliqua</p>
      <a class="btn">Learn More</a>
    </article>
    <article class="service-card">
      <div class="service-photo" role="img" aria-label="Flower garden with purple and red blooms" style="background:linear-gradient(180deg,#3f6e22,#7aa63a 55%,#8a6aa8)"></div>
      <span class="service-icon"><svg width="30" height="30" viewBox="0 0 30 30" fill="none" stroke="#9dbd1d" stroke-width="2"><path d="M3 11l12-6 12 6-12 6zM3 16l12 6 12-6M3 21l12 6 12-6"/></svg></span>
      <h3>Land Beautification</h3>
      <p>Lorem ipsum dolor sit amet, consur adipiscing elit, sed do eiusmod tempor iniduntut labore et dolore magna aliqua</p>
      <a class="btn">Learn More</a>
    </article>
  </div>
</section>

<section class="welcome">
  <div class="welcome-photo" role="img" aria-label="Curved stone-edged garden beds with shrubs and lawn"></div>
  <div class="welcome-kicker">WELCOME TO</div>
  <h2 class="welcome-title display">TOMLET BUILDERS</h2>
  <p class="welcome-text">Lorem ipsum dolor sit amet, consectetur adipiscing elit, sed do eiusmod tempor incididunt ut labore et dolore aliqua. Qs ipm suspendisse ultrices gravida. Risus commodo viverra maecenas accumsan lacus l fciis. Lorem ipsum dolor sit amet, consectetur adipiscing elit, sed do eiusmod tempor incididunt ut labore et dolore magna aliqua. Quis ism suspendisse ultrices gravida. Risus commodo viverra maecenas accumsan lacus vl sis. Lorem ipsum dolor sit amet, consectetur adipiscing elit, sed do eiusmod tempor incididunt ut labore et dolore aliqua. Qs ipm suesse ultres gravida. Risus commodo viverra maecenas accumsan lacus vel facilisis.</p>
  <a class="btn">Learn More</a>
</section>

<section class="why">
  <h2 class="section-title display" style="top:2440px">WHY CHOOSE US</h2>
  <div class="feature left" style="left:100px;top:2525px">
    <span class="feature-icon"><svg width="38" height="38" viewBox="0 0 38 38" fill="none" stroke="#fff" stroke-width="2.5"><circle cx="19" cy="13" r="7"/><path d="M19 9v8M16 11h5M16 15h5M5 28l6-4h9l8-4M5 33h22l8-6"/></svg></span>
    <h3>Competitive Rates</h3>
    <p>Lorem ipsum dolor sit at, consectetur adipiscing elit, sedo eiusmod tempor incididunt ut labore et dolore magna aliqua. Quis ipsum suspendisse</p>
  </div>
  <div class="feature right" style="left:735px;top:2525px">
    <span class="feature-icon"><svg width="38" height="38" viewBox="0 0 38 38" fill="#fff"><circle cx="19" cy="12" r="7"/><path d="M6 33c0-8 6-12 13-12s13 4 13 12z"/></svg></span>
    <h3>Highly Experienced</h3>
    <p>Lorem ipsum dolor sit at, consectetur adipiscing elit, sedo eiusmod tempor incididunt ut labore et dolore magna aliqua. Quis ipsum suspendisse</p>
  </div>
  <div class="divider" style="left:100px"></div>
  <div class="divider" style="left:735px"></div>
  <div class="center-brand"><div class="brand-mark"></div><span>TOMLET<br>BUILDERS</span></div>
  <div class="feature left" style="left:100px;top:2694px">
    <span class="feature-icon"><svg width="38" height="38" viewBox="0 0 38 38" fill="none" stroke="#fff" stroke-width="2.5"><circle cx="19" cy="16" r="10"/><circle cx="19" cy="16" r="4"/><path d="M13 25l-3 9 5-2 3 4M25 25l3 9-5-2-3 4"/></svg></span>
    <h3>Excellent Workmanship</h3>
    <p>Lorem ipsum dolor sit at, consectetur adipiscing elit, sedo eiusmod tempor incididunt ut labore et dolore magna aliqua. Quis ipsum suspendisse</p>
  </div>
  <div class="feature right" style="left:735px;top:2694px">
    <span class="feature-icon" style="font:700 44px Georgia,serif;color:#fff;padding-top:18px">&ldquo;</span>
    <h3>Free Quotations</h3>
    <p>Lorem ipsum dolor sit at, consectetur adipiscing elit, sedo eiusmod tempor incididunt ut labore et dolore magna aliqua. Quis ipsum suspendisse</p>
  </div>
</section>

<section class="testimonials" role="img" aria-label="Soft-focus lawn mower on a sunlit lawn behind a light overlay">
  <h2 class="section-title display">TESTIMONIALS</h2>
  <div class="quote-mark"><i></i>&ldquo;<i></i></div>
  <p class="quote-text">Lorem ipsum dolor sit amet, consectetur adipiscing elit, sed do eiusmod temr incididunt ut labore et dolore magna aliqua. Quis ipsum suspendisse ultrices gravida. Rus commodo viverra maecenas accumsan lacus vel facilisis. Lorem ipsum dolor sit amet, consectr adipiscing elit, sed do eiusmod temr incididunt ut labore et dolore magna aliqua. Quis ipsum suspendisse ultrices gravida. Rus commodo viverra maecenas accumsan lacus vel facilisis. Lorem ipsum dolor sit amet</p>
  <svg class="t-arrow" style="left:146px" width="34" height="34" viewBox="0 0 34 34"><circle cx="17" cy="17" r="15.5" fill="none" stroke="#222" stroke-width="1.5"/><path d="M20 10l-7 7 7 7" fill="none" stroke="#222" stroke-width="1.5"/></svg>
  <svg class="t-arrow" style="left:1030px" width="34" height="34" viewBox="0 0 34 34"><circle cx="17" cy="17" r="15.5" fill="none" stroke="#222" stroke-width="1.5"/><path d="M14 10l7 7-7 7" fill="none" stroke="#222" stroke-width="1.5"/></svg>
  <div class="reviewer"><span class="avatar" role="img" aria-label="Reviewer portrait"></span><div><strong>MARK ELLISON</strong><small>United Kingdom</small></div></div>
</section>

<section class="projects">
  <h2 class="section-title display" style="top:3445px">LATEST PROJECTS</h2>
  <div class="project" style="left:105px;top:3515px">
    <div class="half" role="img" aria-label="Before: bare soil yard" style="background:linear-gradient(180deg,#4f6b35,#7a6a58 40%,#8a7b6a)"></div>
    <div class="half" role="img" aria-label="After: new green lawn" style="background:linear-gradient(180deg,#4f6b35,#5f9a2c 45%,#72a83a)"></div>
    <span class="project-toggle"><svg width="14" height="18" viewBox="0 0 14 18"><path d="M3 2l8 7-8 7" fill="none" stroke="#222" stroke-width="1.8"/></svg></span>
  </div>
  <div class="project" style="left:607px;top:3515px">
    <div class="half" role="img" aria-label="Before: overgrown shrub" style="background:linear-gradient(180deg,#6c8a4a,#3f6a26 50%,#5e7d3e)"></div>
    <div class="half" role="img" aria-label="After: neatly trimmed round shrub" style="background:linear-gradient(180deg,#8aa56a,#3d6e22 50%,#6a8f45)"></div>
    <span class="project-toggle"><svg width="14" height="18" viewBox="0 0 14 18"><path d="M3 2l8 7-8 7" fill="none" stroke="#222" stroke-width="1.8"/></svg></span>
  </div>
  <div class="project" style="left:105px;top:3841px">
    <div class="half" role="img" aria-label="Before: cluttered backyard of an old house" style="background:linear-gradient(180deg,#bfc3c2,#8f8a7c 55%,#8a6d4c)"></div>
    <div class="half" role="img" aria-label="After: renovated house with garden steps" style="background:linear-gradient(180deg,#d4d6d4,#6e7478 50%,#5f7e3e)"></div>
    <span class="project-toggle"><svg width="14" height="18" viewBox="0 0 14 18"><path d="M3 2l8 7-8 7" fill="none" stroke="#222" stroke-width="1.8"/></svg></span>
  </div>
  <div class="project" style="left:607px;top:3841px">
    <div class="half" role="img" aria-label="Before: bare side yard with bins" style="background:linear-gradient(180deg,#e2e2de,#b7b6ac 50%,#7f7a5c)"></div>
    <div class="half" role="img" aria-label="After: side yard with flower beds" style="background:linear-gradient(180deg,#e4e4e0,#6f9a3c 55%,#c75a7a)"></div>
    <span class="project-toggle"><svg width="14" height="18" viewBox="0 0 14 18"><path d="M3 2l8 7-8 7" fill="none" stroke="#222" stroke-width="1.8"/></svg></span>
  </div>
  <a class="btn abs" style="left:500px;top:4183px;width:200px;height:42px">View All Projects</a>
</section>

<section class="cta" role="img" aria-label="Garden path lit by lamps at dusk">
  <h2 class="display">CALL TODAY FOR A FREE ESTIMATES,<br>NO OBLIGATION QUOTE ON</h2>
  <div class="phone-box">
    <span class="phone-icon"><svg width="24" height="24" viewBox="0 0 24 24"><path d="M6.6 10.8a15 15 0 0 0 6.6 6.6l2.2-2.2c.3-.3.7-.4 1-.2 1.1.4 2.3.6 3.6.6.6 0 1 .4 1 1V20c0 .6-.4 1-1 1A17 17 0 0 1 3 4c0-.6.4-1 1-1h3.5c.6 0 1 .4 1 1 0 1.3.2 2.5.6 3.6.1.3 0 .7-.2 1z" fill="none" stroke="#fff" stroke-width="1.6"/></svg></span>
    <span class="phone-number">555 014 7720</span>
  </div>
  <a class="btn">Contact Us</a>
</section>

<footer class="site-footer">
  <div class="footer-brand"><div class="brand-mark"></div><span>TOMLET<br>BUILDERS</span></div>
  <div class="footer-col" style="left:399px">
    <h4>Quick Links</h4>
    <ul><li>Home</li><li>About us</li><li>Services</li><li>Projects</li><li>Review</li><li>Contact us</li></ul>
  </div>
  <div class="footer-col" style="left:643px">
    <h4>Contact Us</h4>
    <div class="contact-row"><span class="contact-icon"><svg width="16" height="20" viewBox="0 0 16 20"><path d="M8 1a7 7 0 0 0-7 7c0 5 7 11 7 11s7-6 7-11a7 7 0 0 0-7-7z" fill="#111"/><circle cx="8" cy="8" r="2.5" fill="#fff"/></svg></span><span>4821 Meadow Lane Springfield<br>USA 21930</span></div>
    <div class="contact-row"><span class="contact-icon"><svg width="18" height="18" viewBox="0 0 24 24"><path d="M6.6 10.8a15 15 0 0 0 6.6 6.6l2.2-2.2c.3-.3.7-.4 1-.2 1.1.4 2.3.6 3.6.6.6 0 1 .4 1 1V20c0 .6-.4 1-1 1A17 17 0 0 1 3 4c0-.6.4-1 1-1h3.5c.6 0 1 .4 1 1 0 1.3.2 2.5.6 3.6.1.3 0 .7-.2 1z" fill="#111"/></svg></span><span>Call Us<br>555 014 7720</span></div>
    <div class="contact-row"><span class="contact-icon"><svg width="18" height="14" viewBox="0 0 18 14"><rect x="1" y="1" width="16" height="12" fill="#111"/><path d="M1 1l8 7 8-7" stroke="#fff" stroke-width="1.4" fill="none"/></svg></span><span>E mail us<br>info@tomletbuilders.com</span></div>
  </div>
  <div class="footer-col social" style="left:1007px">
    <h4>Follow Us</h4>
    <ul><li>Friendbook</li><li>Chirper</li><li>Linkline</li><li>Snapgram</li></ul>
  </div>
  <div class="footer-rule"></div>
  <p class="copyright">© 2020 TOMLET BUILDERS. All Rights Reserved.</p>
</footer>

</body>
</html>
```